Brookmere Osteopathy flyer

I want a clean clear DL flyer (but also want an A4 poster) promoting a new Osteopathic business in a semi rural area in Tasmania (Australia).
It can have pictures like the examples attached to show people what Osteopathy is (its like Chiropractic and physiotherapy).
I am the sole practioner and am male, so any pictures would be best to be a white male if possible.
I've attached some wording, you can use all, or none of it
I don't have a phone number for the business yet
info@brookmereosteopathy.example
www.brookmereosteopathy.example
Target Market(s)
Australians, from tradies, professionals, babies to retired people
Industry/Entity Type
Health
Look and feel

```html
<!DOCTYPE html>
<html lang="en">
<head>
<meta charset="utf-8">
<title>Brookmere Osteopathy – DL Flyer</title>
<link rel="stylesheet" href="https://fonts.googleapis.com/css2?family=Nunito:wght@400;600;700&family=Saira+Condensed:wght@600;700&family=Oswald:wght@400;500&family=Marcellus&display=swap">
<style>
:root{
  --blue:#1a8bcf;
  --blue-deep:#1479b8;
  --orange:#f7952f;
  --ink:#1c1c1c;
  --white:#ffffff;
  --page:#eceae6;
}
*{box-sizing:border-box;margin:0;padding:0}
html,body{width:1191px;height:1200px;overflow:hidden;background:var(--page)}
body{position:relative;font-family:"Nunito",sans-serif;color:var(--ink)}
.panel{position:absolute;top:86px;width:483px;height:1025px;background:var(--white);overflow:hidden;box-shadow:0 4px 14px rgba(0,0,0,.18)}
.panel--front{left:92px}
.panel--back{left:612px;width:485px}
.abs{position:absolute}

/* front */
.top-band{left:0;top:0;width:100%;height:45px;background:var(--blue);border-bottom:2px solid var(--orange)}
.brand-mark{left:20px;top:16px;width:136px;height:136px;border-radius:50%;background:var(--white);border:3px solid var(--blue);display:flex;align-items:center;justify-content:center;text-align:center;font-weight:700;font-size:15px;line-height:1.2;color:var(--blue);padding:14px}
.brand-name{left:168px;top:62px;font-size:27.5px;font-weight:600;color:var(--blue);letter-spacing:.4px;white-space:nowrap}
.tagline{left:168px;top:92px;font-family:"Saira Condensed",sans-serif;font-weight:600;font-size:36px;color:var(--orange);white-space:nowrap;line-height:1.2}
.intro{left:11px;top:160px;width:457px;font-size:14.8px;line-height:28.6px;text-align:justify;letter-spacing:.5px}
.photo{background:linear-gradient(135deg,#e8eef3,#c9d6e0)}
.photo--spine{left:0;top:375px;width:100%;height:280px;background:linear-gradient(120deg,#dfe6ec 0%,#eef2f5 45%,#cfdbe5 100%)}
.photo--baby{left:1px;top:657px;width:236px;height:186px;background:linear-gradient(160deg,#a7a9c6,#8aa3c4 60%,#b8c2d6)}
.photo--back{left:248px;top:657px;width:233px;height:186px;background:linear-gradient(135deg,#2f4a62,#c9a77f 55%,#eed9b4)}
.serving{left:0;top:860px;width:100%;text-align:center;font-size:17.5px;font-weight:700;letter-spacing:.3px}
.offer{font-family:"Saira Condensed",sans-serif;font-weight:700;letter-spacing:.5px;white-space:nowrap}
.offer--front{left:0;top:890px;width:100%;text-align:center;font-size:35px;color:var(--blue)}
.spine-accent{left:4px;top:932px;width:472px;height:58px}
.address--front{left:34px;top:984px;display:flex;align-items:center;gap:14px;font-size:23px;white-space:nowrap}

/* back */
.photo--hero{left:0;top:0;width:100%;height:323px;background:linear-gradient(100deg,#f3f4f4 0%,#e7ebec 45%,#c9d3d6 70%,#e9a04a 88%,#f2a533 100%)}
.hero-title{left:23px;top:66px;font-family:"Oswald",sans-serif;font-weight:400;font-size:37px;line-height:44px;color:#111;letter-spacing:-.6px}
.list-title{left:11px;top:346px;font-family:"Saira Condensed",sans-serif;font-weight:700;font-size:28px;color:var(--blue);white-space:nowrap}
.reasons{left:11px;top:390px;list-style:none}
.reasons li{display:flex;align-items:center;height:37px;font-size:19px;letter-spacing:.3px;white-space:nowrap}
.reasons svg{width:22px;height:16px;margin-right:19px;flex:none}
.offer--back{left:0;top:780px;width:100%;text-align:center;font-size:35px;color:var(--orange)}
.contact-band{left:0;top:857px;width:100%;height:168px;background:var(--blue);color:var(--white)}
.phone-icon{left:15px;top:30px;width:40px;height:46px}
.visit{left:69px;top:22px;font-size:15.5px;font-weight:600;letter-spacing:.3px}
.phone{left:69px;top:40px;font-family:"Marcellus",serif;font-size:32px;letter-spacing:.5px}
.band-mark{left:392px;top:11px;width:82px;height:82px;border-radius:50%;border:2px solid var(--white);display:flex;align-items:center;justify-content:center;text-align:center;font-size:10px;font-weight:700;line-height:1.2;padding:8px}
.address--back{left:15px;top:98px;display:flex;align-items:center;gap:16px;font-size:22px;white-space:nowrap}
.web-row{left:12px;right:12px;top:140px;display:flex;align-items:center;justify-content:space-between;font-size:11px;white-space:nowrap}
.web-item{display:flex;align-items:center;gap:6px}
.web-row svg{width:12px;height:12px;flex:none}
</style>
</head>
<body>

<section class="panel panel--front">
  <div class="abs top-band"></div>
  <div class="abs brand-mark">Brookmere Osteopathy</div>
  <h1 class="abs brand-name">Brookmere Osteopathy</h1>
  <p class="abs tagline">Move Better, Feel Better.</p>
  <p class="abs intro">Brookmere Osteopathy use a tailored combination of joint mobilisation/manipulation, stretching, movement, trigger point dry needling and targeted massage to reduce pain and restore optimal function. Hands-on treatment is backed up with rehabilitative exercise prescription and advice. So whether you're recovering from injury or managing chronic discomfort, we're here to help you move better &amp; feel your best.</p>
  <div class="abs photo photo--spine" role="img" aria-label="Practitioner pointing to a model of the human spine and pelvis"></div>
  <div class="abs photo photo--baby" role="img" aria-label="Newborn baby receiving gentle cranial osteopathy"></div>
  <div class="abs photo photo--back" role="img" aria-label="Practitioner treating a woman's lower back"></div>
  <p class="abs serving">Serving Semi Rural Area In Tasmania - Australia</p>
  <p class="abs offer offer--front">FREE INTIAL PHYSIO CONSULTATION</p>
  <svg class="abs spine-accent" viewBox="0 0 472 58" role="img" aria-label="Faint spine decoration">
    <path d="M0 58 C120 40 300 20 472 0 L472 14 C300 36 140 52 0 58Z" fill="#d6e8f5"/>
  </svg>
  <div class="abs address--front">
    <svg width="22" height="30" viewBox="0 0 22 30"><path d="M11 0C4.9 0 0 4.9 0 11c0 8 11 19 11 19s11-11 11-19C22 4.9 17.1 0 11 0zm0 15.5a4.5 4.5 0 1 1 0-9 4.5 4.5 0 0 1 0 9z" fill="var(--orange)"/></svg>
    <span>48 Willow Creek Road, Brookmere</span>
  </div>
</section>

<section class="panel panel--back">
  <div class="abs photo photo--hero" role="img" aria-label="Practitioner stretching a smiling male patient's shoulder in a bright clinic"></div>
  <h2 class="abs hero-title">CHIROPRACTIC<br>AND<br>PHYSIOTHERAPY</h2>
  <h3 class="abs list-title">Common Reasons People Visit An Osteopath</h3>
  <ul class="abs reasons">
    <li><svg viewBox="0 0 22 16"><path d="M2 15C3 8 8 5 14 5V1l7 6-7 6V9C9 9 5 11 2 15Z" fill="var(--orange)"/></svg>Back / Neck Pain</li>
    <li><svg viewBox="0 0 22 16"><path d="M2 15C3 8 8 5 14 5V1l7 6-7 6V9C9 9 5 11 2 15Z" fill="var(--orange)"/></svg>Headaches / Migraines</li>
    <li><svg viewBox="0 0 22 16"><path d="M2 15C3 8 8 5 14 5V1l7 6-7 6V9C9 9 5 11 2 15Z" fill="var(--orange)"/></svg>Joint And Muscle Pain</li>
    <li><svg viewBox="0 0 22 16"><path d="M2 15C3 8 8 5 14 5V1l7 6-7 6V9C9 9 5 11 2 15Z" fill="var(--orange)"/></svg>Pregnancy-related Discomfort</li>
    <li><svg viewBox="0 0 22 16"><path d="M2 15C3 8 8 5 14 5V1l7 6-7 6V9C9 9 5 11 2 15Z" fill="var(--orange)"/></svg>Disc Related Issues</li>
    <li><svg viewBox="0 0 22 16"><path d="M2 15C3 8 8 5 14 5V1l7 6-7 6V9C9 9 5 11 2 15Z" fill="var(--orange)"/></svg>Sciatica</li>
    <li><svg viewBox="0 0 22 16"><path d="M2 15C3 8 8 5 14 5V1l7 6-7 6V9C9 9 5 11 2 15Z" fill="var(--orange)"/></svg>Plantar Fasciitis</li>
    <li><svg viewBox="0 0 22 16"><path d="M2 15C3 8 8 5 14 5V1l7 6-7 6V9C9 9 5 11 2 15Z" fill="var(--orange)"/></svg>Tendonitis / Bursitis</li>
    <li><svg viewBox="0 0 22 16"><path d="M2 15C3 8 8 5 14 5V1l7 6-7 6V9C9 9 5 11 2 15Z" fill="var(--orange)"/></svg>Adhesive Capsulitis (Frozen Shoulder)</li>
    <li><svg viewBox="0 0 22 16"><path d="M2 15C3 8 8 5 14 5V1l7 6-7 6V9C9 9 5 11 2 15Z" fill="var(--orange)"/></svg>Tennis / Golfers Elbow</li>
  </ul>
  <p class="abs offer offer--back">FREE INTIAL PHYSIO CONSULTATION</p>

  <footer class="abs contact-band">
    <svg class="abs phone-icon" viewBox="0 0 40 46" fill="none" stroke="#fff" stroke-width="2.2" stroke-linejoin="round" stroke-linecap="round">
      <path d="M9 4l6 9-4 4c2 6 6 11 11 15l4-4 9 6-4 7C18 40 3 22 5 8Z"/>
      <path d="M22 10a10 10 0 0 1 8 8M23 4a16 16 0 0 1 13 13"/>
    </svg>
    <p class="abs visit">Visit Us Today</p>
    <p class="abs phone">03 5550 0199</p>
    <div class="abs band-mark">Brookmere Osteopathy</div>
    <div class="abs address--back">
      <svg width="20" height="28" viewBox="0 0 22 30"><path d="M11 0C4.9 0 0 4.9 0 11c0 8 11 19 11 19s11-11 11-19C22 4.9 17.1 0 11 0zm0 15.5a4.5 4.5 0 1 1 0-9 4.5 4.5 0 0 1 0 9z" fill="#fff"/></svg>
      <span>48 Willow Creek Road, Brookmere</span>
    </div>
    <div class="abs web-row">
      <span class="web-item">
        <svg viewBox="0 0 14 14" fill="none" stroke="#fff" stroke-width="1.3"><rect x="1" y="3" width="12" height="9" rx="1"/><path d="M1 4l6 4 6-4"/></svg>
        <span>info@brookmereosteopathy.example</span>
      </span>
      <span class="web-item">
        <svg viewBox="0 0 14 14" fill="none" stroke="#fff" stroke-width="1.1"><circle cx="7" cy="7" r="6"/><ellipse cx="7" cy="7" rx="2.6" ry="6"/><path d="M1 7h12"/></svg>
        <span>www.brookmereosteopathy.example</span>
      </span>
    </div>
  </footer>
</section>

</body>
</html>
```